Civora88 - a Political Plebescite app.

There is a current app in the App Store (worldwide) and Play Store (worldwide) called yourStance (with an owl logo). The UX needs to be redesigned to make it more visually pleasing.

The requirement is to build a UX that is suitable for both iOS and Android - i.e. consistent look for both platforms. The design is to span the variety of sizes available from smart devices - phones and tablets. The layout as it stands is portrait only, and a secondary design to encompass landscape is wanted.

You would need to download the app to get a feel for all the functionality - there are 3 visible forms (currently) and a hidden form, that will be used in the near future - this hidden form will look similar to the main (first) form.

To get full functionality you need to do the following:
Go to the Options page
Toggle the top slide
Click on UNREGISTERED
Select a state/territory

I know this is a bit non-intuitive - in the "real" product these steps are automated - but for this release the user gets to choose.

Once this is done - the other button(s) appear in the top left of the screen - and data is available to be displayed.

The current forms are included in this brief. The Options screen will ultimately not be showing all the current data, only the lower slider (or other indicator) and the associated version and copyright notices. The hidden screen is much like the main screen - showing the name of the bill and information pertaining to that bill - there needs to be a button (or action site) to toggle between the main and this hidden screen.

Target Market(s)

All eligable voters (currently in Australia)

Industry/Entity Type

Political

Requirements
Should not have
• Do not present to me my own/existing design with the only change being colours and label layout.

```html
<!DOCTYPE html>
<html lang="en">
<head>
<meta charset="utf-8">
<title>Civora88 – Bill Vote Screen</title>
<link href="https://fonts.googleapis.com/css2?family=Roboto:wght@300;400;500;700&display=swap" rel="stylesheet">
<style>
  :root {
    --page-bg: #ffffff;
    --bar-bg: #f7f7f8;
    --rule: #d4d4d6;
    --ink: #111111;
    --ink-soft: #444444;
    --link-blue: #1a82fb;
    --card-blue: #007aff;
    --online-green: #2ecc71;
    --yes-green: #2ecc71;
    --abstain-yellow: #f5d76e;
    --no-red: #ec6349;
    --footer-grey: #efefef;
    --card-edge: #d9d9d9;
  }
  * { box-sizing: border-box; margin: 0; padding: 0; }
  html, body {
    width: 1200px; height: 1200px; overflow: hidden;
    background: var(--page-bg);
    font-family: "Roboto", "Helvetica Neue", Arial, sans-serif;
    color: var(--ink);
  }
  .screen {
    position: absolute; left: 281px; top: 36px;
    width: 580px; height: 1026px;
    transform: scale(1.1); transform-origin: top left;
    background: #fff;
    border: 1px solid var(--rule);
    overflow: hidden;
  }
  .top-bars { position: absolute; left: 0; top: 0; width: 100%; height: 115px; background: var(--bar-bg); border-bottom: 1px solid var(--rule); }
  .status-bar { position: absolute; top: 8px; left: 10px; right: 8px; height: 22px; font-size: 17px; font-weight: 500; }
  .status-signal { position: absolute; left: 0; top: 2px; }
  .status-time { position: absolute; left: 0; right: 0; text-align: center; }
  .status-battery { position: absolute; right: 0; top: 0; font-weight: 300; display: flex; align-items: center; gap: 3px; }
  .nav-bar { position: absolute; top: 52px; left: 0; right: 0; height: 60px; }
  .nav-online { position: absolute; left: 20px; top: 26px; font-size: 16px; font-weight: 400; display: flex; align-items: center; gap: 9px; }
  .nav-online::before { content: ""; width: 12px; height: 12px; border-radius: 50%; background: var(--online-green); }
  .nav-title { position: absolute; left: 0; right: 0; top: 3px; text-align: center; }
  .nav-kicker { font-size: 12px; font-weight: 500; letter-spacing: .2px; }
  .nav-region { font-size: 25px; font-weight: 300; margin-top: 4px; display: inline-flex; align-items: center; gap: 12px; }
  .nav-region::before { content: ""; border: 6px solid transparent; border-top: 6px solid var(--ink); border-bottom: 0; margin-left: -10px; }
  .nav-settings { position: absolute; right: 18px; top: 24px; font-size: 21px; font-weight: 300; color: var(--link-blue); }
  .progress { position: absolute; top: 140px; left: 0; right: 0; text-align: center; font-size: 22px; font-weight: 700; }
  .card-stack { position: absolute; left: 34px; top: 218px; width: 504px; height: 600px; }
  .card-under { position: absolute; background: #fff; border: 1px solid var(--card-edge); border-radius: 10px; height: 60px; }
  .card-under.second { left: 6px; right: 6px; top: 550px; }
  .card-under.third { left: 12px; right: 12px; top: 558px; }
  .bill-card { position: absolute; inset: 0 0 auto 0; height: 569px; background: #fff; border-radius: 10px; border: 1px solid var(--card-edge); box-shadow: 0 1px 3px rgba(0,0,0,.2); overflow: hidden; }
  .bill-head { background: var(--card-blue); color: #fff; height: 153px; padding: 20px 18px 0 26px; font-weight: 700; }
  .bill-name { font-size: 20px; line-height: 26px; }
  .bill-year { font-size: 20px; margin-top: 15px; }
  .bill-summary { padding: 26px 24px 0 31px; font-size: 23px; line-height: 29px; font-weight: 300; }
  .bill-footer { position: absolute; left: 0; right: 0; bottom: 0; height: 71px; background: var(--footer-grey); border-top: 1px solid #e2e2e2; text-align: center; line-height: 71px; font-size: 22px; font-weight: 700; color: var(--ink-soft); }
  .vote-row { position: absolute; top: 860px; left: 0; right: 0; height: 122px; }
  .vote-button { position: absolute; top: 0; width: 121px; height: 121px; margin-left: -60px; border-radius: 50%; background: #fff; border: 1px solid #dcdcdc; box-shadow: 0 1px 3px rgba(0,0,0,.15); display: flex; align-items: center; justify-content: center; }
  .vote-face { width: 103px; height: 103px; border-radius: 50%; display: flex; align-items: center; justify-content: center; }
  .vote-yes { left: 140px; } .vote-yes .vote-face { background: var(--yes-green); }
  .vote-abstain { left: 289px; } .vote-abstain .vote-face { background: var(--abstain-yellow); }
  .vote-no { left: 436px; } .vote-no .vote-face { background: var(--no-red); }
</style>
</head>
<body>
<main class="screen">
  <header class="top-bars">
    <div class="status-bar">
      <svg class="status-signal" width="80" height="16" viewBox="0 0 80 16" aria-hidden="true">
        <g fill="#111"><circle cx="5" cy="8" r="4"/><circle cx="15" cy="8" r="4"/><circle cx="25" cy="8" r="4"/><circle cx="35" cy="8" r="4"/><circle cx="45" cy="8" r="4"/></g>
        <path d="M55 6 a11 11 0 0 1 16 0 M58 9 a7 7 0 0 1 10 0" stroke="#111" stroke-width="2" fill="none"/>
        <circle cx="63" cy="12.5" r="2" fill="#111"/>
      </svg>
      <div class="status-time">9:41 AM</div>
      <div class="status-battery">100%
        <svg width="40" height="18" viewBox="0 0 40 18" aria-hidden="true"><rect x="1" y="2" width="34" height="14" rx="2" fill="#111" stroke="#111"/><rect x="36" y="6" width="3" height="6" fill="#111"/></svg>
      </div>
    </div>
    <nav class="nav-bar">
      <div class="nav-online">ONLINE</div>
      <div class="nav-title">
        <div class="nav-kicker">LEGISLATIVE ASSEMBLY</div>
        <div class="nav-region">Northern Territory</div>
      </div>
      <div class="nav-settings">Settings</div>
    </nav>
  </header>

  <div class="progress">4/10</div>

  <section class="card-stack">
    <div class="card-under third"></div>
    <div class="card-under second"></div>
    <article class="bill-card">
      <div class="bill-head">
        <h2 class="bill-name">Monitoring of Places of Detention (Optional Protocol to the Convention Against Torture) - National Uniform Legislation</h2>
        <div class="bill-year">Bill 2013</div>
      </div>
      <p class="bill-summary">An act to enable the Optional Protocol to the Convention against Torture and other Cruel, Inhuman or Degrading Treatment or Punishment to be given effect within the Territory.</p>
      <div class="bill-footer">VIEW BILL</div>
    </article>
  </section>

  <div class="vote-row">
    <div class="vote-button vote-yes" aria-label="Vote yes"><div class="vote-face">
      <svg width="44" height="40" viewBox="0 0 44 40" aria-hidden="true"><g fill="#1b1b1b"><path d="M2 18 h12 l7-14 c1-3 6-3 6 1 v8 h0 l-2 3 v20 H6 c-2 0-4-2-4-4z"/><rect x="30" y="17" width="10" height="22" rx="1"/></g></svg>
    </div></div>
    <div class="vote-button vote-abstain" aria-label="Abstain"><div class="vote-face">
      <svg width="42" height="38" viewBox="0 0 42 38" aria-hidden="true"><g fill="#1b1b1b"><path d="M21 1 L40 10 v4 H2 v-4z"/><rect x="2" y="32" width="38" height="5"/><path d="M4 16 h34 v14 H4z M9 19 v9 h3 v-9z M15 19 v9 h3 v-9z M21 19 v9 h3 v-9z M27 19 v9 h3 v-9z" fill-rule="evenodd"/></g></svg>
    </div></div>
    <div class="vote-button vote-no" aria-label="Vote no"><div class="vote-face">
      <svg width="44" height="40" viewBox="0 0 44 40" aria-hidden="true"><g fill="#1b1b1b" transform="rotate(180 22 20)"><path d="M2 18 h12 l7-14 c1-3 6-3 6 1 v8 h0 l-2 3 v20 H6 c-2 0-4-2-4-4z"/><rect x="30" y="17" width="10" height="22" rx="1"/></g></svg>
    </div></div>
  </div>
</main>
</body>
</html>
```